New Business Card Design Project

I need a design for business cards, i am an electrical business called "Corvane Electrical and Communications" i need the cards to be double sided with the company logo on the back (attached) the front needs to say my company name, web site, email address, telephone number, and ABN number and electrical license number. I am open to different arrangements of the information but would like the background to be incorporating something electrical or something that looks smart. open to all additional ideas also.

The company colours are orange and grey see logo attached.

Business Name: Corvane Electrical and Communications
Website: corvaneelectricalandcomms.example.com.au
Email: brent@corvaneelectricalandcomms.example.com.au
Telephone(mobile): 0481209736
ABN: 71208349162
Lic No: 418273D

Target Market(s)

Business entities, Project Managers, Accounts, Clients

Industry/Entity Type

Electrician

Contact Information for Business Card

I need a design for business cards, i am an electrical business called "Corvane Electrical and Communications" i need the cards to be double sided with the company logo on the back (attached) the front needs to say my company name

Font styles to use
Serif
Sans Serif

Colors
f37122
5c5c5c

Requirements
Must have
• Must have the Logo on the back open to different ways of it being on the back but had in mind to keep it central but again open to other options
Nice to have
• A real modern cool background that is eye catching yet contemporary
Should not have
• No backgrounds of a light bulb or plug or anything like that

```html
<!DOCTYPE html>
<html lang="en">
<head>
<meta charset="utf-8">
<title>Corvane Electrical and Communications – Business Card</title>
<link href="https://fonts.googleapis.com/css2?family=Rajdhani:wght@600;700&family=Arimo:wght@400&family=Open+Sans:wght@400&display=swap" rel="stylesheet">
<style>
  :root {
    --backdrop: #333335;
    --card-grey: #58585a;
    --accent: #f9ad1a;
    --white: #ffffff;
    --rule: #8a8a8c;
  }
  * { margin: 0; padding: 0; box-sizing: border-box; }
  html, body { width: 1105px; height: 1200px; overflow: hidden; }
  body { background: var(--backdrop); position: relative; font-family: "Arimo", Arial, sans-serif; }

  .card { position: absolute; left: 196px; width: 720px; height: 410px; overflow: hidden; }

  /* Front */
  .card-front { top: 146px; background: var(--card-grey); }
  .brand { position: absolute; left: 34px; top: 158px; width: 270px; color: var(--white);
           font-family: "Rajdhani", sans-serif; font-weight: 600; }
  .brand-mark { display: inline-block; width: 14px; height: 14px; border-radius: 50%;
                background: var(--accent); margin-right: 10px; vertical-align: 8px; }
  .brand-name { font-size: 58px; line-height: 1; letter-spacing: 3px; }
  .brand-tagline { display: block; font-size: 13.5px; letter-spacing: 1px; margin-top: 6px; }

  .divider { position: absolute; left: 326px; top: 106px; width: 1px; height: 220px; background: var(--rule); }

  .contact { position: absolute; left: 354px; top: 100px; color: var(--white); }
  .person-name { font-family: "Rajdhani", sans-serif; font-weight: 700; font-size: 29px;
                 color: var(--accent); line-height: 1; letter-spacing: .5px; }
  .person-role { font-family: "Rajdhani", sans-serif; font-weight: 700; font-size: 20px;
                 line-height: 1; margin-top: 8px; }
  .registration { margin-top: 24px; font-size: 18px; line-height: 28px; }
  .contact-list { list-style: none; margin-top: 12px; }
  .contact-list li { display: flex; align-items: center; font-size: 18px; height: 27px; }
  .contact-list li.small { font-size: 14.5px; letter-spacing: -.3px; }
  .contact-list svg { width: 16px; height: 16px; margin-right: 11px; flex: none; }

  .edge-line { position: absolute; left: 0; top: 374px; width: 100%; height: 3px; background: #e9e9e9; }
  .edge-band { position: absolute; left: 0; top: 380px; width: 100%; height: 30px; background: var(--accent); }

  /* Back */
  .card-back { top: 602px; background: var(--accent); }
  .back-brand { position: absolute; left: 0; top: 168px; width: 100%; text-align: center;
                font-family: "Rajdhani", sans-serif; font-weight: 600; font-size: 84px;
                letter-spacing: 6px; color: var(--white); line-height: 1; }
  .back-web { position: absolute; left: 0; top: 330px; width: 100%; text-align: center;
              font-family: "Open Sans", sans-serif; font-size: 17px; letter-spacing: 1.6px; color: var(--white); }
</style>
</head>
<body>

<section class="card card-front">
  <div class="brand">
    <span class="brand-mark"></span><span class="brand-name">CORVANE</span>
    <span class="brand-tagline">ELECTRICAL &amp; COMMUNICATIONS</span>
  </div>

  <div class="divider"></div>

  <div class="contact">
    <p class="person-name">Dana Whitlock</p>
    <p class="person-role">CEO/Founder</p>
    <p class="registration">ABN: 71208349162<br>Lic No: 418273D</p>
    <ul class="contact-list">
      <li>
        <svg viewBox="0 0 16 16" aria-hidden="true"><rect x="3.5" y="1" width="9" height="14" rx="1.5" fill="none" stroke="var(--accent)" stroke-width="2"/><rect x="6.5" y="12" width="3" height="1.2" fill="var(--accent)"/></svg>
        0481209736
      </li>
      <li class="small">
        <svg viewBox="0 0 16 16" aria-hidden="true"><rect x="1" y="3.5" width="14" height="9.5" fill="var(--accent)"/><path d="M1.5 4 L8 9 L14.5 4" fill="none" stroke="var(--card-grey)" stroke-width="1.3"/></svg>
        brent@corvaneelectricalandcomms.example.com.au
      </li>
      <li class="small">
        <svg viewBox="0 0 16 16" aria-hidden="true"><circle cx="8" cy="8" r="7" fill="var(--accent)"/><path d="M5 4.5 Q7 5 6.5 7 Q5 8 6 10 M10 3.5 Q9 6 11 7.5 Q12.5 9 11 12" fill="none" stroke="var(--card-grey)" stroke-width="1.3"/></svg>
        corvaneelectricalandcomms.example.com.au
      </li>
    </ul>
  </div>

  <div class="edge-line"></div>
  <div class="edge-band"></div>
</section>

<section class="card card-back">
  <p class="back-brand">CORVANE</p>
  <p class="back-web">www.corvaneelectricalandcomms.example.com.au</p>
</section>

</body>
</html>
```